Brell Stone Company Business Cards

Front and Back Business Card - logo and text setup - cool design. I need workable photoshop or illustrator files so I can setup each employee card with design that is created
Updates

Hi everyone, thank you for the great entries. Please no more white and blue cards - there are so many already - black and silver only now please. thanks!

Target Market(s)

Construction Industry - Facility Managers

Industry/Entity Type

Construction

Contact Information for Business Card

I really like contemporary simplistic looks - clean neat....not opposed to seeing some black backrounds

Requirements
Must have
• Logo/website address with design on front only - www.brellstone-example.com (logo attached)
• Back:
• Name/Title/Company Address/Phone/email address
Nice to have
• Cool design
Should not have
• Nothing gimmicky like Fire or Water - since we are a Fire Protection company - it has all been done

```html
<!DOCTYPE html>
<html lang="en">
<head>
<meta charset="utf-8">
<title>Brell Stone Company Business Cards</title>
<link href="https://fonts.googleapis.com/css2?family=Lato:wght@400;700;900&display=swap" rel="stylesheet">
<style>
  :root {
    --backdrop: #1b1b1b;
    --card-dark: #111111;
    --card-silver: #d9dadc;
    --silver: #c4c6c9;
    --silver-deep: #7d8085;
    --ink-black: #141414;
    --ink: #333333;
  }
  * { margin: 0; padding: 0; box-sizing: border-box; }
  html, body {
    width: 1200px;
    height: 800px;
    overflow: hidden;
    background: var(--backdrop);
    font-family: "Lato", sans-serif;
  }
  .canvas {
    position: relative;
    width: 1200px;
    height: 800px;
    background: var(--backdrop);
  }
  .card {
    position: absolute;
    border-radius: 2px;
  }
  .card-front {
    left: 260px;
    top: 108px;
    width: 313px;
    height: 534px;
    background: var(--card-dark);
  }
  .brand-name {
    position: absolute;
    left: 0;
    right: 0;
    top: 224px;
    text-align: center;
    color: var(--silver);
    font-weight: 900;
    font-size: 40px;
    line-height: 48px;
    letter-spacing: -0.5px;
  }
  .front-web {
    position: absolute;
    left: 0;
    right: 0;
    bottom: 36px;
    text-align: center;
    color: var(--silver-deep);
    font-size: 13px;
    letter-spacing: 0.8px;
  }
  .card-back {
    left: 629px;
    top: 115px;
    width: 317px;
    height: 528px;
    background: var(--card-silver);
    padding: 52px 38px 0;
  }
  .person-name {
    color: var(--ink-black);
    font-weight: 700;
    font-size: 25px;
    line-height: 1.1;
  }
  .person-title {
    color: var(--silver-deep);
    font-weight: 700;
    font-size: 17px;
    line-height: 1.2;
  }
  .contact {
    position: absolute;
    left: 38px;
    top: 308px;
    color: var(--ink);
    font-size: 16px;
    line-height: 19.5px;
  }
  .contact-address { margin-bottom: 10px; }
  .contact-lines { margin-bottom: 20px; }
  .contact-web { letter-spacing: 0.6px; }
</style>
</head>
<body>
<main class="canvas">
  <section class="card card-front">
    <div class="brand-name">Brell Stone</div>
    <div class="front-web">www.brellstone-example.com</div>
  </section>
  <section class="card card-back">
    <div class="person-name">Dana Whitlow</div>
    <div class="person-title">CEO/Founder</div>
    <div class="contact">
      <p class="contact-address">48-2 Harbor Park<br>Road, Lake<br>Marrow, NY 10492</p>
      <p class="contact-lines">P. (555) 014-2287<br>F. (555) 014-2290<br>info@brellstone-example.com</p>
      <p class="contact-web">www.brellstone-example.com</p>
    </div>
  </section>
</main>
</body>
</html>
```